SkyvornQ Business Cards and Stationary Design

Need a design for our business cards and stationary. I want to carry on the theme of the logo. I want the business cards to have a design on the back. I would like the business cards and the stationary to carry the same theme, design scheme, and branding

Target Market(s)

Airlines and Maintenance Facilities

Industry/Entity Type

Aviation

Contact Information for Business Card

Name
Position Title
Address: 4827 Trellis Hollow Road, Fort Pierce, Florida, 34951
Office Number
Mobile Number
Email
Website

Font styles to use
Serif
Sans Serif

Colors

Designer to choose colors to be used in the design.

```html
<!DOCTYPE html>
<html lang="en">
<head>
<meta charset="utf-8">
<title>SkyvornQ Business Cards</title>
<link rel="stylesheet" href="https://fonts.googleapis.com/css2?family=Open+Sans:wght@400;600;700&display=swap">
<style>
  :root {
    --backdrop: #e8e5e2;
    --card: #ffffff;
    --navy: #1b3766;
    --sky: #2a8fd6;
    --ink: #4a4f57;
    --rule: #b9bcc2;
  }
  * { box-sizing: border-box; margin: 0; padding: 0; }
  html, body {
    width: 1200px;
    height: 997px;
    overflow: hidden;
    background: var(--backdrop);
    font-family: "Open Sans", Arial, sans-serif;
  }
  .sheet {
    width: 1200px;
    height: 997px;
    display: flex;
    align-items: center;
    justify-content: center;
    gap: 56px;
  }
  .card {
    position: relative;
    width: 520px;
    height: 297px;
    background: var(--card);
    box-shadow: 0 2px 10px rgba(0,0,0,0.08);
  }

  /* brand mark */
  .brand {
    display: flex;
    align-items: center;
    gap: 12px;
    color: var(--navy);
    font-weight: 700;
    letter-spacing: 0.08em;
  }
  .brand-dot {
    border-radius: 50%;
    background: var(--sky);
    flex: none;
  }

  /* front */
  .card-front .brand {
    position: absolute;
    top: 40px;
    right: 40px;
    font-size: 26px;
  }
  .card-front .brand-dot { width: 30px; height: 30px; }
  .card-front .divider {
    position: absolute;
    top: 104px;
    left: 40px;
    right: 40px;
    height: 1px;
    background: var(--rule);
  }
  .contact {
    position: absolute;
    left: 40px;
    bottom: 38px;
    padding-left: 16px;
    border-left: 4px solid var(--navy);
    color: var(--ink);
    font-size: 11.5px;
    line-height: 1.6;
  }
  .contact-name {
    color: var(--navy);
    font-weight: 700;
    font-size: 15px;
    letter-spacing: 0.02em;
    line-height: 1.3;
  }
  .contact-role { margin-bottom: 6px; }
  .contact-label { color: var(--navy); font-weight: 700; }
  .contact-gap { margin-right: 8px; }

  /* back */
  .card-back {
    display: flex;
    flex-direction: column;
    align-items: center;
    justify-content: center;
  }
  .card-back .brand {
    flex-direction: column;
    gap: 14px;
    font-size: 38px;
  }
  .card-back .brand-dot { width: 58px; height: 58px; }
  .web-line {
    display: flex;
    align-items: center;
    gap: 14px;
    margin-top: 16px;
    color: var(--navy);
    font-size: 12px;
    letter-spacing: 0.18em;
  }
  .web-line::before, .web-line::after {
    content: "";
    width: 60px;
    height: 1px;
    background: var(--navy);
  }
</style>
</head>
<body>
<main class="sheet">
  <section class="card card-front" aria-label="Business card front">
    <div class="brand"><span class="brand-dot"></span>SkyvornQ</div>
    <div class="divider"></div>
    <div class="contact">
      <div class="contact-name">DANIEL HARROW</div>
      <div class="contact-role">President</div>
      <div>
        <span class="contact-label">T.:</span> <span class="contact-gap">001 555 0148</span>
        <span class="contact-label">M.:</span> <span class="contact-gap">+001 555 0193</span>
        <span class="contact-label">E.:</span> info@skyvornq.com
      </div>
      <div><span class="contact-label">A.:</span> 4827 Trellis Hollow Road, Fort Pierce, Florida, 34951</div>
    </div>
  </section>

  <section class="card card-back" aria-label="Business card back">
    <div class="brand"><span class="brand-dot"></span>SkyvornQ</div>
    <div class="web-line">www.skyvornq.com</div>
  </section>
</main>
</body>
</html>
```